New business card for a regional office of a US M&A company

We need business card for a finance company, office based in Hong Kong , our Head office is in US, our business is to Merge and acquires companies , the new office will be a regional office for the Asia Pacific region. We want to use the head office logo as attached ( but don't have to be exactly the same, can be a variation to it) as a base and then add Asia Pacific alongside the logo.
We would prefer to have be bilingual Eng + Chinese, although we don't really have Chinese company name .

Industry/Entity Type

Business

Contact Information for Business Card

Clara Jo Tsang
 

VP,
APAC M&A Operations
Orin Vantage Asia Pacific Limited
 
Unit 1407, K18
18 Tai Lok Shan Road, 
Hong Kong 
 
M: +852 6038 1742
T : +852 2836 4100
F : +852 2836 4177
VOIP: 4158
 
cjtsang@orinvantage.com

Font styles to use
Serif
Sans Serif

Colors

Designer to choose colors to be used in the design.

Requirements
Must have
• APAC Office

```html
<!DOCTYPE html>
<html lang="en">
<head>
<meta charset="utf-8">
<title>Orin Vantage Asia Pacific – Business Card</title>
<link rel="stylesheet" href="https://fonts.googleapis.com/css2?family=Ubuntu:wght@400;500;700&display=swap">
<style>
  :root {
    --backdrop: #e6e7e8;
    --card-navy: #0e2740;
    --brand-blue: #1fa3cf;
    --band-blue: #1d98bd;
    --text-white: #f2f5f8;
    --icon-grey: #b9c7d4;
    --divider: #2a4a66;
  }
  * { margin: 0; padding: 0; box-sizing: border-box; }
  html, body { width: 1200px; height: 576px; overflow: hidden; }
  body {
    background: var(--backdrop);
    font-family: "Ubuntu", sans-serif;
    position: relative;
  }
  .card {
    position: absolute;
    width: 484px;
    height: 292px;
    background: var(--card-navy);
    border-radius: 11px;
    overflow: hidden;
    box-shadow: 0 3px 8px rgba(0,0,0,0.25);
  }
  .card-front { left: 82px; top: 139px; }
  .card-back { left: 602px; top: 138px; }

  /* front */
  .front-band {
    position: absolute; left: 0; right: 0; bottom: 0;
    height: 7px; background: var(--band-blue);
  }
  .front-brand {
    position: absolute; left: 0; right: 0; top: 90px;
    display: flex; flex-direction: column; align-items: center; gap: 22px;
  }
  .brand-square {
    width: 26px; height: 26px; background: var(--text-white);
  }
  .front-wordmark {
    font-weight: 700; font-size: 43px; letter-spacing: 1px;
    color: var(--brand-blue); line-height: 1;
  }

  /* back */
  .back-wordmark {
    position: absolute; left: 10px; width: 212px; top: 118px;
    text-align: center;
    font-weight: 700; font-size: 24px; color: var(--text-white);
  }
  .back-divider {
    position: absolute; left: 228px; top: 52px;
    width: 1px; height: 160px; background: var(--divider);
  }
  .contact-block {
    position: absolute; left: 258px; top: 47px;
    color: var(--text-white);
  }
  .holder-name {
    font-weight: 500; font-size: 17px; color: var(--brand-blue);
    line-height: 20px;
  }
  .holder-title {
    margin-top: 4px; font-size: 12px; line-height: 16px;
  }
  .company-name {
    margin-top: 26px; font-weight: 500; font-size: 13px;
    color: var(--brand-blue); line-height: 16px;
  }
  .contact-list { list-style: none; margin-top: 10px; }
  .contact-list li {
    display: flex; align-items: center; gap: 9px;
    font-size: 12px; line-height: 15px;
  }
  .contact-list svg { width: 10px; height: 10px; fill: var(--icon-grey); flex: none; }
  .voip-label { color: var(--brand-blue); margin-left: 4px; }
  .address-band {
    position: absolute; left: 0; right: 0; bottom: 0; height: 28px;
    background: var(--band-blue);
    color: var(--text-white); font-size: 12px;
    display: flex; align-items: center; justify-content: center;
  }
</style>
</head>
<body>
  <section class="card card-front">
    <div class="front-brand">
      <div class="brand-square"></div>
      <div class="front-wordmark">ORIN VANTAGE</div>
    </div>
    <div class="front-band"></div>
  </section>

  <section class="card card-back">
    <div class="back-wordmark">Orin Vantage</div>
    <div class="back-divider"></div>
    <div class="contact-block">
      <h1 class="holder-name">Clara Jo Tsang</h1>
      <p class="holder-title">Vice President,<br>APAC M&amp;A Operations</p>
      <p class="company-name">Orin Vantage Asia Pacific Limited</p>
      <ul class="contact-list">
        <li>
          <svg viewBox="0 0 10 10" aria-hidden="true"><path d="M2.5 0h5a1 1 0 0 1 1 1v8a1 1 0 0 1-1 1h-5a1 1 0 0 1-1-1V1a1 1 0 0 1 1-1zm.3 1.3v6h4.4v-6zM5 8a.6.6 0 1 0 0 1.2A.6.6 0 0 0 5 8z"/></svg>
          <span>+852 6038 1742</span>
        </li>
        <li>
          <svg viewBox="0 0 10 10" aria-hidden="true"><path d="M0 3.2C0 1.6 2.2 1 5 1s5 .6 5 2.2v.8H7.3v-.9H2.7V4H0zM2.5 4.6h5L9.3 7v2H.7V7zM5 5.6a1.2 1.2 0 1 0 0 2.4 1.2 1.2 0 0 0 0-2.4z"/></svg>
          <span>+852 2836 4100</span>
        </li>
        <li>
          <svg viewBox="0 0 10 10" aria-hidden="true"><path d="M2.5 0h5v3h-5zM1 3.5h8a1 1 0 0 1 1 1V8H8V6.5H2V8H0V4.5a1 1 0 0 1 1-1zM2.7 7h4.6v3H2.7z"/></svg>
          <span>+852 2836 4177,</span><span class="voip-label">VOIP:</span><span style="margin-left:-6px">4158</span>
        </li>
        <li>
          <svg viewBox="0 0 10 10" aria-hidden="true"><path d="M0 2h10v.6L5 5.6 0 2.6zM0 3.6l5 3 5-3V8H0z"/></svg>
          <span>cjtsang@orinvantage.com</span>
        </li>
      </ul>
    </div>
    <div class="address-band">Unit 1407, K18 18, Tai Lok Shan Road, Hong Kong</div>
  </section>
</body>
</html>
```